Business Card for Field Lotus-Eco Friendly Organic Clothing Brand

We are looking for an amazing business card for our eco friendly, organic clothing brand. We are thinking maybe a business card with a peel off sticker on the back, since our hanging clothing tag is a peel off sticker on the back. I will attach our hang tag so we can make sure we stay in line with our design. I've also attached a bag we are doing because I do like the scattered emblem look as well.

```html
<!DOCTYPE html>
<html lang="en">
<head>
<meta charset="utf-8">
<title>Field Lotus – Business Card</title>
<link rel="stylesheet" href="https://fonts.googleapis.com/css2?family=Open+Sans:wght@400;600;700&display=swap">
<style>
  :root {
    --backdrop: #e9e6e2;
    --card-white: #ffffff;
    --camo-dark: #1b1f13;
    --camo-mid: #2a2f1d;
    --gold: #e3b84f;
    --gold-muted: #8a7a4a;
    --text-light: #f3f1ea;
    --icon-gold: #d9ac45;
  }
  * { box-sizing: border-box; margin: 0; padding: 0; }
  html, body {
    width: 1200px; height: 900px; overflow: hidden;
    background: var(--backdrop);
    font-family: "Open Sans", Arial, sans-serif;
  }
  .canvas { position: relative; width: 1200px; height: 900px; }

  .card {
    position: absolute;
    background: var(--card-white);
    box-shadow: 0 6px 18px rgba(0,0,0,0.18);
    overflow: hidden;
  }
  .card--front { left: 77px; top: 34px; width: 590px; height: 364px; }
  .card--back  { left: 388px; top: 505px; width: 567px; height: 352px; }

  .camo-band {
    position: absolute; left: 0; right: 0;
    background: linear-gradient(135deg, var(--camo-mid), var(--camo-dark));
  }
  .card--front .camo-band { top: 168px; bottom: 0; }
  .card--back .camo-band { top: 83px; height: 180px; }

  .brand-mark {
    position: absolute; left: 38px; top: 58px;
    display: flex; align-items: center; gap: 12px;
  }
  .brand-mark__square { width: 22px; height: 22px; background: var(--gold); }
  .brand-mark__name { font-size: 30px; font-weight: 700; color: var(--gold); }
  .brand-mark__url {
    position: absolute; left: 72px; top: 100px;
    font-size: 12px; color: var(--gold-muted);
  }

  .contact-block {
    position: absolute; left: 31px; top: 196px; color: var(--text-light);
  }
  .contact-block__name {
    font-size: 21px; line-height: 28px; font-weight: 400; color: var(--gold); letter-spacing: 0.3px;
  }
  .contact-block__title { font-size: 15px; line-height: 20px; margin-top: 0; }
  .contact-list { list-style: none; margin-top: 31px; }
  .contact-list li {
    display: flex; align-items: center; gap: 8px;
    font-size: 15px; line-height: 21px;
  }
  .contact-list svg { width: 13px; height: 13px; fill: var(--icon-gold); flex: none; }

  .back-brand__name {
    position: absolute; left: 0; right: 0; top: 118px;
    text-align: center; color: #ffffff;
    font-size: 46px; font-weight: 700; line-height: 64px;
  }
  .back-brand__url {
    position: absolute; left: 0; right: 0; top: 226px;
    text-align: center; color: #e8e8e2;
    font-size: 17px; line-height: 24px;
  }
</style>
</head>
<body>
<main class="canvas">

  <section class="card card--front">
    <div class="brand-mark">
      <span class="brand-mark__square"></span>
      <span class="brand-mark__name">Field Lotus</span>
    </div>
    <span class="brand-mark__url">www.fieldlotus.com</span>

    <div class="camo-band" role="img" aria-label="Dark olive camouflage pattern with a faint silhouette of a meditating figure"></div>

    <div class="contact-block">
      <p class="contact-block__name">Daniel Reyes</p>
      <p class="contact-block__title">Managing Director</p>
      <ul class="contact-list">
        <li>
          <svg viewBox="0 0 16 16" aria-hidden="true"><path d="M3.6 1.5l2.3 2.6-1.3 1.8c.9 1.9 2.4 3.4 4.3 4.3l1.8-1.3 2.6 2.3-1.2 2.1C7.4 13.8 2.2 8.6 1.5 3.9z"/></svg>
          044-987 650 312
        </li>
        <li>
          <svg viewBox="0 0 16 16" aria-hidden="true"><path d="M1 3h14v10H1z M1.8 3.8L8 8.6l6.2-4.8" stroke="#1b1f13" stroke-width="1"/></svg>
          info@fieldlotus.com
        </li>
        <li>
          <svg viewBox="0 0 16 16" aria-hidden="true"><path d="M6.5 9.5l3-3M7 4.5l1.8-1.8a2.4 2.4 0 013.4 3.4L10.5 7.8M9 11.5l-1.8 1.8a2.4 2.4 0 01-3.4-3.4L5.5 8.2" stroke="#d9ac45" stroke-width="1.8" fill="none"/></svg>
          www.fieldlotusco.com
        </li>
      </ul>
    </div>
  </section>

  <section class="card card--back">
    <div class="camo-band" role="img" aria-label="Dark olive camouflage pattern"></div>
    <span class="back-brand__name">Field Lotus</span>
    <span class="back-brand__url">www.fieldlotus.com</span>
  </section>

</main>
</body>
</html>
```